Website for steady harbor detailing.

Need a homepage, pages for: car and truck detailing, boat detailing, airplane detailing, about us, contact us. I have the domain name through nimbushelm so I will need the design uploaded on my domain. Also hoping to link other domains to this page.I would like to see the logo more pronounced. I would like to see a large phone number link to call my business. The layout looks nice but the pics need to depict car washing and waxing not car mechanics. i would like the colors of the webpage to incorporate the colors found in the logo in some way. I would like links to social media pages
Updates

Target Market(s)

Local customers in Vero Beach, Florida.

Number of Pages Required

5+ page

Colors

Requirements
Must have
• Easy to navigate, attractive pages with pictures and logo, professional looking. must have my phone number and logo very prevalent and links to call or go to home page. I would like links to my social media accounts on the home page.
Nice to have
• Easy to navigate, attractive pages with pictures and logo, professional looking.

```html
<!DOCTYPE html>
<html lang="en">
<head>
<meta charset="utf-8">
<title>Steady Harbor Detailing</title>
<link href="https://fonts.googleapis.com/css2?family=Raleway:wght@400;600;700;800&family=Open+Sans:ital,wght@0,400;0,600;1,400;1,600&display=swap" rel="stylesheet">
<style>
:root{
  --red:#e8423c;
  --red-deep:#d8302b;
  --navy:#2b2e82;
  --navy-dark:#262a78;
  --sky:#12a3e6;
  --ink:#333;
  --muted:#777;
  --white:#fff;
}
*{margin:0;padding:0;box-sizing:border-box}
html,body{width:716px;height:1200px;overflow:hidden;background:#fff}
body{position:relative;font-family:"Open Sans",sans-serif;color:var(--ink)}
.abs{position:absolute}

/* header */
.topband{left:0;top:0;width:716px;height:62px;background:radial-gradient(circle at 30% 40%,#f26a63,var(--red) 60%,var(--red-deep))}
.navbar{left:0;top:62px;width:716px;height:37px;background:#fff;box-shadow:0 1px 3px rgba(0,0,0,.15)}
.brand{left:48px;top:22px;display:flex;align-items:center;gap:8px}
.brand-dot{width:14px;height:14px;border-radius:50%;background:var(--white)}
.brand-name{font-family:"Raleway",sans-serif;font-weight:800;font-size:16px;line-height:17px;color:var(--white);text-transform:uppercase}
.callbox{left:530px;top:16px;display:flex;gap:8px}
.callbox small{display:block;font-family:"Raleway",sans-serif;font-weight:700;font-size:8px;color:var(--navy)}
.callbox strong{display:block;font-family:"Raleway",sans-serif;font-weight:700;font-size:16px;color:#fff;margin-top:1px}
.menu{left:256px;top:76px;display:flex;align-items:center;gap:15px;font-size:8.2px;color:#222;text-transform:uppercase}
.menu a{color:inherit;text-decoration:none}

/* hero */
.hero{left:0;top:99px;width:716px;height:305px;background:linear-gradient(180deg,#3f66a8 0%,#6a8fc0 30%,#7a7f80 60%,#555 100%)}
.hero-band{left:0;top:364px;width:716px;height:40px;background:linear-gradient(90deg,rgba(232,66,60,0) 15%,rgba(232,66,60,.85) 40%,rgba(232,66,60,.85) 60%,rgba(232,66,60,0) 85%)}
.hero-title{left:0;top:373px;width:716px;text-align:center;font-family:"Raleway",sans-serif;font-weight:700;font-size:18px;color:#fff;text-transform:uppercase}
.hero-arrow{top:373px}

/* services */
.services{left:0;top:404px;width:716px;height:284px;background:linear-gradient(180deg,#fff 0%,#fff 56%,#d6d6ea 68%,#6f73b8 100%)}
.card{top:443px;width:199px;height:202px;background:#fff;box-shadow:0 1px 3px rgba(0,0,0,.12)}
.card-photo{left:0;top:0;width:199px;height:124px}
.card-tab{left:0;top:0}
.card-tab span{position:absolute;left:10px;top:8px;font-family:"Raleway",sans-serif;font-weight:700;font-size:11px;color:#fff;white-space:nowrap}
.card-text{left:15px;top:137px;width:172px;font-size:8px;line-height:15px;color:var(--muted)}
.card-arrow{right:10px;bottom:7px}

/* welcome */
.welcome-sub{left:48px;top:742px;font-family:"Raleway",sans-serif;font-size:15px;color:var(--navy)}
.welcome-title{left:48px;top:765px;font-family:"Raleway",sans-serif;font-weight:800;font-size:21.5px;color:var(--navy)}
.welcome-copy{left:47px;top:802px;width:340px;font-size:7.9px;line-height:16px;color:#666}
.welcome-copy p+p{margin-top:3px}
.btn{left:46px;top:924px;width:102px;height:30px;background:linear-gradient(90deg,var(--navy),var(--sky));color:#fff;font-family:"Raleway",sans-serif;font-weight:700;font-size:12px;display:flex;align-items:center;justify-content:center;text-decoration:none}
.agent{left:450px;top:703px;width:205px;height:115px;background:linear-gradient(180deg,#f4f4f4,#e6e6e6);border-radius:60px 60px 8px 8px}
.promo-shadow{left:425px;top:950px;width:245px;height:14px;background:radial-gradient(ellipse at center top,rgba(0,0,0,.28),rgba(0,0,0,0) 70%)}
.promo{left:421px;top:803px;width:249px;height:149px;background:var(--navy)}
.promo-inner{left:7px;top:7px;width:235px;height:136px;background:var(--red);color:#fff;text-align:center}
.promo-inner p{margin-top:33px;font-size:8.8px;line-height:17.5px;padding:0 20px}
.promo-inner a{display:block;margin-top:18px;color:#fff;font-style:italic;font-weight:600;font-size:15px;text-decoration:underline}

/* footer */
.footer{left:0;top:992px;width:716px;height:208px;background:var(--navy-dark)}
.contact{top:1018px;width:160px;text-align:center;color:#fff}
.contact .icon{width:46px;height:46px;border-radius:50%;background:var(--red);margin:0 auto;display:flex;align-items:center;justify-content:center}
.contact h3{margin-top:12px;font-family:"Raleway",sans-serif;font-weight:700;font-size:12.5px}
.contact p{font-size:9px;margin-top:1px;letter-spacing:.2px}
.rule{left:46px;top:1124px;width:624px;height:1px;background:rgba(255,255,255,.22)}
.footlinks{left:0;top:1147px;width:716px;text-align:center;font-size:8px;color:#fff}
.footlinks a{color:#fff;text-decoration:none}
.footlinks i{font-style:normal;margin:0 7px}
.copyright{left:0;top:1164px;width:716px;text-align:center;font-size:8px;color:#fff}
</style>
</head>
<body>

<header>
  <div class="abs topband"></div>
  <div class="abs navbar"></div>
  <a class="abs brand" href="#" style="text-decoration:none">
    <span class="brand-dot"></span>
    <span class="brand-name">Steady Harbor<br>Detailing</span>
  </a>
  <div class="abs callbox">
    <svg width="28" height="30" viewBox="0 0 24 24"><path fill="#12a3e6" d="M6.6 10.8a15.1 15.1 0 0 0 6.6 6.6l2.2-2.2c.3-.3.7-.4 1-.2 1.1.4 2.3.6 3.6.6.6 0 1 .4 1 1V20c0 .6-.4 1-1 1A17 17 0 0 1 3 4c0-.6.4-1 1-1h3.5c.6 0 1 .4 1 1 0 1.3.2 2.5.6 3.6.1.3 0 .7-.2 1z"/></svg>
    <div><small>Call Us Today :</small><strong>555 214 0187</strong></div>
  </div>
  <nav class="abs menu">
    <svg width="11" height="10" viewBox="0 0 24 22"><path fill="#2b2e82" d="M12 1 1 11h3v10h6v-6h4v6h6V11h3z"/></svg>
    <a href="#">Car &amp; Truck Detailing</a>
    <a href="#">Boat Detailing</a>
    <a href="#">Airplane Detailing</a>
    <a href="#">About Us</a>
    <a href="#">Contact Us</a>
  </nav>
</header>

<section>
  <div class="abs hero" role="img" aria-label="Photo of a detailer pressure-washing a silver car outside a garage"></div>
  <div class="abs hero-band"></div>
  <h1 class="abs hero-title">Steady Harbor Detailing</h1>
  <svg class="abs hero-arrow" style="left:172px" width="12" height="22" viewBox="0 0 12 22"><path d="M10 1 2 11l8 10" fill="none" stroke="#fff" stroke-width="1.6"/></svg>
  <svg class="abs hero-arrow" style="left:531px" width="12" height="22" viewBox="0 0 12 22"><path d="M2 1l8 10-8 10" fill="none" stroke="#fff" stroke-width="1.6"/></svg>
</section>

<section>
  <div class="abs services"></div>

  <article class="abs card" style="left:46px">
    <div class="abs card-photo" role="img" aria-label="Photo of a red sports car being hand washed with foam" style="background:linear-gradient(135deg,#b9a99a,#d8d2cc 45%,#c4574f 70%,#9c8d80)"></div>
    <svg class="abs card-tab" width="160" height="28" viewBox="0 0 160 28"><defs><linearGradient id="tg1" x1="0" x2="1"><stop offset="0" stop-color="#2b2e82"/><stop offset="1" stop-color="#12a3e6"/></linearGradient></defs><path d="M0 0h146l14 14-14 14H0z" fill="url(#tg1)"/></svg>
    <div class="abs card-tab"><span>CAR &amp; TRUCK DETAILING</span></div>
    <p class="abs card-text">Lorem Ipsum is simply dummy text of the printing and typesetting industry. Lorem Ipsum has been the industry</p>
    <svg class="abs card-arrow" width="16" height="8" viewBox="0 0 16 8"><path d="M0 4h14M10 1l4 3-4 3" fill="none" stroke="#12a3e6" stroke-width="1.6"/></svg>
  </article>

  <article class="abs card" style="left:258px">
    <div class="abs card-photo" role="img" aria-label="Photo of a white and black motor yacht on a trailer being cleaned" style="background:linear-gradient(180deg,#8fb6dc,#d6e2ec 45%,#3a3a3a 62%,#7d7d70)"></div>
    <svg class="abs card-tab" width="160" height="28" viewBox="0 0 160 28"><path d="M0 0h146l14 14-14 14H0z" fill="url(#tg1)"/></svg>
    <div class="abs card-tab"><span>BOAT DETAILING</span></div>
    <p class="abs card-text">Lorem Ipsum is simply dummy text of the printing and typesetting industry. Lorem Ipsum has been the industry</p>
    <svg class="abs card-arrow" width="16" height="8" viewBox="0 0 16 8"><path d="M0 4h14M10 1l4 3-4 3" fill="none" stroke="#12a3e6" stroke-width="1.6"/></svg>
  </article>

  <article class="abs card" style="left:471px">
    <div class="abs card-photo" role="img" aria-label="Photo of a worker cleaning the underside of a small airplane" style="background:linear-gradient(180deg,#e9ebee,#cfd3d8 40%,#3d5f8c 58%,#6d6d6d)"></div>
    <svg class="abs card-tab" width="160" height="28" viewBox="0 0 160 28"><path d="M0 0h146l14 14-14 14H0z" fill="url(#tg1)"/></svg>
    <div class="abs card-tab"><span>AIRPLANE DETAILING</span></div>
    <p class="abs card-text">Lorem Ipsum is simply dummy text of the printing and typesetting industry. Lorem Ipsum has been the industry</p>
    <svg class="abs card-arrow" width="16" height="8" viewBox="0 0 16 8"><path d="M0 4h14M10 1l4 3-4 3" fill="none" stroke="#12a3e6" stroke-width="1.6"/></svg>
  </article>
</section>

<section>
  <div class="abs welcome-sub">WELCOME TO</div>
  <h2 class="abs welcome-title">STEADY HARBOR DETAILING</h2>
  <div class="abs welcome-copy">
    <p>Lorem Ipsum is simply dummy text of the printing and typesetting industry. Lorem Ipsum has been the industry's standard dummy text ever since the 1500s, when an unknown printer took a galley of type and scrambled.</p>
    <p>Lorem Ipsum is simply dummy text of the printing and typesetting industry. Lorem Ipsum has been the industry's standard dummy text ever since the 1500s, when an unknown printer took a galley of type and scrambled it to make a type specimen book. It has survived not only five centuries, but also the leap.</p>
  </div>
  <a class="abs btn" href="#">LEARN MORE</a>

  <div class="abs agent" role="img" aria-label="Photo of a smiling customer service agent with a headset leaning on the panel"></div>
  <div class="abs promo-shadow"></div>
  <div class="abs promo">
    <div class="abs promo-inner">
      <p>Our Professional Car Wash Services Will Thoroughly Clean Your Car or Truck While Being Gentle On Its Finish.</p>
      <a href="tel:5552140187">Call Us On : 555 214 0187</a>
    </div>
  </div>
</section>

<footer>
  <div class="abs footer"></div>
  <div class="abs contact" style="left:59px">
    <div class="icon"><svg width="18" height="22" viewBox="0 0 24 30"><path fill="#fff" d="M12 0a10 10 0 0 0-10 10c0 7.5 10 20 10 20s10-12.5 10-20A10 10 0 0 0 12 0zm0 14a4 4 0 1 1 0-8 4 4 0 0 1 0 8z"/></svg></div>
    <h3>Address</h3><p>Steady Harbor Detailing</p>
  </div>
  <div class="abs contact" style="left:278px">
    <div class="icon"><svg width="20" height="20" viewBox="0 0 24 24"><path fill="#fff" d="M6.6 10.8a15.1 15.1 0 0 0 6.6 6.6l2.2-2.2c.3-.3.7-.4 1-.2 1.1.4 2.3.6 3.6.6.6 0 1 .4 1 1V20c0 .6-.4 1-1 1A17 17 0 0 1 3 4c0-.6.4-1 1-1h3.5c.6 0 1 .4 1 1 0 1.3.2 2.5.6 3.6.1.3 0 .7-.2 1z"/></svg></div>
    <h3>Phone</h3><p>555 214 0187</p>
  </div>
  <div class="abs contact" style="left:483px">
    <div class="icon"><svg width="20" height="15" viewBox="0 0 24 18"><path fill="#fff" d="M0 2a2 2 0 0 1 2-2h20a2 2 0 0 1 2 2v.5l-12 7-12-7zm0 3 12 7 12-7v11a2 2 0 0 1-2 2H2a2 2 0 0 1-2-2z"/></svg></div>
    <h3>Email</h3><p>info@steadyharbor.com</p>
  </div>
  <div class="abs rule"></div>
  <nav class="abs footlinks">
    <a href="#">Car And Truck Detailing</a><i>|</i><a href="#">Boat Detailing</a><i>|</i><a href="#">Airplane Detailing</a><i>|</i><a href="#">About Us</a><i>|</i><a href="#">Contact Us</a>
  </nav>
  <div class="abs copyright">©STEADY HARBOR DETAILING &nbsp;- 2018 All Rights Reserved Privacy Policy</div>
</footer>

</body>
</html>
```